Vento Hallmark Real estate Costa del sol

we need a website for our Company based in Costa del sol, Spain. We sell properties on the spanish coast that is called costa del sol. We are concentrating on exclusive properties and would like the webdesign to show this. In our website we want to have area descriptions of the different areas we sell our Products. We will also implement a searchable database delivered by a third part where all properties for sale in Spain are listed. When looking into the designs we would like our main page to have a overview of the coast where the different areas are shown. Have a look at brightlunavista.example or oakterra.example to see. The webpage will be presented in 4 languages, English, spanish, Swedish and norwegian, and shall of course also be prepared for social medias. We want an easy Contemporary design but still with an exclusive feeling!
Scandinavian and North european Citizens wants to buy a property in Spain
Real Estate
5+ page

```html
<!DOCTYPE html>
<html lang="en">
<head>
<meta charset="utf-8">
<title>Vento Hallmark — Real Estate Costa del Sol</title>
<link rel="stylesheet" href="https://fonts.googleapis.com/css2?family=Tinos:wght@400;700&family=Open+Sans:wght@400;600;700&display=swap">
<style>
:root{
  --navy:#121a4a;
  --navy-deep:#0c1238;
  --ink:#222;
  --muted:#666;
  --dark:#2b2b2b;
  --darker:#232323;
  --panel:#333;
  --field:#3c3c3c;
  --light:#f3f3f3;
  --line:#dcdcdc;
  --white:#fff;
  --map-deep:#1f4d7a;
  --map-mid:#2f6496;
  --map-land:#5d7e9d;
}
*{box-sizing:border-box;margin:0;padding:0}
html,body{width:1200px;height:2970px;overflow:hidden}
body{position:relative;font-family:"Open Sans",Arial,sans-serif;color:var(--ink);background:var(--white);font-size:12px}
.serif{font-family:"Tinos","Times New Roman",serif}
.abs{position:absolute}

/* hero */
.hero{position:absolute;left:0;top:0;width:1200px;height:594px;overflow:hidden}
.hero-map{position:absolute;inset:0;background:
  radial-gradient(ellipse 380px 220px at 330px 260px,var(--map-land),transparent 70%),
  radial-gradient(ellipse 300px 240px at 880px 240px,var(--map-land),transparent 70%),
  radial-gradient(ellipse 160px 120px at 1000px 470px,#6d8aa4,transparent 70%),
  linear-gradient(180deg,var(--map-mid),var(--map-deep))}
.topbar{position:absolute;left:594px;top:0;width:606px;height:34px;background:#1b1b1b;display:flex;align-items:center;color:#eee;font-size:12px}
.social{display:flex}
.social span{width:34px;height:34px;display:block;border-right:1px solid #333;position:relative}
.social span::after{content:"";position:absolute;left:13px;top:13px;width:8px;height:8px;background:#ddd;border-radius:50%}
.social span.on{background:#4a4a4a}
.lang{margin-left:20px;display:flex;align-items:center;gap:6px;font-size:11px}
.lang i{width:14px;height:9px;background:#c8102e;display:block}
.call{margin-left:26px;padding-left:20px;border-left:1px solid #444;display:flex;align-items:center;gap:8px;font-size:14px}
.navbar{position:absolute;left:0;top:34px;width:1200px;height:69px;background:rgba(248,248,248,.93)}
.brand{position:absolute;left:162px;top:10px;display:flex;align-items:center;gap:10px}
.brand b{width:26px;height:26px;border:3px solid var(--navy);display:block}
.brand span{font-family:"Tinos","Times New Roman",serif;font-size:22px;color:var(--navy)}
.menu{position:absolute;top:24px;left:450px;display:flex;font-size:13px;color:#333}
.menu a{text-decoration:none;color:inherit;position:absolute;white-space:nowrap}
.menu .active{font-weight:700}
.menu .active::after{content:"";position:absolute;left:0;right:0;bottom:-6px;height:2px;background:var(--navy)}
.slide-arrow{position:absolute;top:310px}
.dots{position:absolute;top:560px;left:0;width:1200px;display:flex;justify-content:center;gap:10px}
.dots i{width:10px;height:10px;border-radius:50%;background:#fff;display:block}
.dots i.on{background:var(--navy);border:2px solid #fff;width:14px;height:14px;margin-top:-2px}

/* search */
.search{position:absolute;left:0;top:594px;width:1200px;height:262px;background:var(--darker)}
.search-form{position:absolute;left:317px;top:46px;width:883px;height:216px;background:var(--panel)}
.tabs{position:absolute;left:317px;top:4px;display:flex;height:42px}
.tab{display:flex;align-items:center;gap:10px;padding:0 24px;color:#fff;font-family:"Tinos",serif;font-size:17px}
.tab.on{background:#5a5a5a;width:202px}
.tab.off{background:#262626;width:161px}
.dream{position:absolute;left:162px;top:92px;color:#fff;text-align:center;width:120px}
.dream small{display:block;font-size:11px;letter-spacing:.5px;margin-bottom:6px}
.dream strong{display:block;font-family:"Tinos",serif;font-weight:400;font-size:33px;line-height:40px}
.field{position:absolute;height:34px;width:217px;background:var(--field);border:1px solid #555;color:#ddd;font-size:11px;display:flex;align-items:center;justify-content:space-between;padding:0 14px}
.field::after{content:"";width:6px;height:6px;border-right:1.5px solid #ddd;border-bottom:1.5px solid #ddd;transform:rotate(45deg);margin-top:-4px}
.range{position:absolute;color:#ddd;font-size:11px}
.range .track{position:absolute;top:24px;left:0;height:3px;background:#777;width:217px}
.range .fill{position:absolute;top:0;height:3px;background:#fff}
.range .knob{position:absolute;top:-5px;width:12px;height:12px;border-radius:50%;background:#fff}
.btn-search{position:absolute;left:824px;top:200px;width:214px;height:34px;background:#fff;color:#222;font-size:11px;display:flex;align-items:center;justify-content:center;gap:8px}

/* headings */
.sec-head{display:flex;align-items:center;gap:14px}
.sec-head b{width:26px;height:26px;border:3px solid var(--navy);display:block}
.sec-head h2{font-family:"Tinos","Times New Roman",serif;font-weight:400;font-size:26px;letter-spacing:.5px;color:var(--navy-deep)}

/* developments */
.developments{position:absolute;left:0;top:856px;width:1200px;height:431px;background:var(--light)}
.pager{position:absolute;display:flex;gap:3px}
.pager span{width:26px;height:24px;background:#ddd;display:flex;align-items:center;justify-content:center}
.pager span.dk{background:#555}
.view-all{position:absolute;left:962px;top:49px;width:76px;height:24px;background:var(--navy);color:#fff;font-size:11px;display:flex;align-items:center;justify-content:center}
.cards{position:absolute;left:162px;top:94px;width:876px;display:flex}
.card{width:219px;height:292px;background:#fff;position:relative;border-right:1px solid #eee}
.card .photo{position:absolute;left:14px;top:20px;width:191px;height:123px}
.card h3{position:absolute;left:14px;top:155px;font-size:11.5px;font-weight:700}
.card .price{position:absolute;left:14px;top:176px;font-size:11px;font-weight:600;width:191px}
.card .price em{position:absolute;right:0;font-style:normal;font-weight:400;color:#444}
.card p{position:absolute;left:14px;top:196px;width:191px;font-size:9.5px;line-height:14px;color:#777}
.card .stats{position:absolute;left:0;bottom:0;width:219px;height:26px;background:var(--navy-deep);color:#fff;font-size:9px;display:flex;align-items:center;justify-content:space-around}
.sale{position:absolute;left:14px;top:20px;background:var(--navy-deep);color:#fff;font-size:9px;padding:3px 10px}
.fav{position:absolute;left:14px;top:20px;width:191px;height:123px;background:rgba(0,0,0,.45)}
.fav small{position:absolute;left:56px;top:14px;background:#333;color:#fff;font-size:8px;padding:2px 8px}
.fav i{position:absolute;top:50px;width:26px;height:26px;border-radius:50%;background:#222;border:1px solid #666}

/* promoted */
.promoted{position:absolute;left:0;top:1287px;width:1200px;height:643px}
.tile{position:absolute;color:#fff;overflow:hidden}
.tile .cap{position:absolute;left:0;right:0;bottom:0;height:70px;background:linear-gradient(transparent,rgba(0,0,0,.7))}
.tile h4{position:absolute;font-family:"Tinos",serif;font-weight:400}
.tile .meta{position:absolute;font-size:10px}
.tile .amt{position:absolute;font-family:"Tinos",serif}

/* testimonials */
.testimonials{position:absolute;left:0;top:1930px;width:1200px;height:363px;background:
  radial-gradient(ellipse 300px 160px at 950px 150px,#4a3c2c,transparent 70%),
  linear-gradient(180deg,#1a1d22,#23262b 60%,#14171b)}
.avatar{position:absolute;left:162px;width:50px;height:50px;background:linear-gradient(#9a9a9a,#555);border:2px solid #ddd}
.quote-box{position:absolute;left:259px;top:145px;width:779px;height:172px;border:1px solid #666;background:rgba(0,0,0,.25);color:#eee;text-align:center}
.quote-box p{font-size:10.5px;line-height:19px;padding:0 50px;margin-top:50px}
.quote-box cite{display:block;font-family:"Tinos",serif;font-style:normal;font-weight:700;font-size:12px;margin-top:8px}

/* clients */
.clients{position:absolute;left:0;top:2293px;width:1200px;height:335px}
.logos{position:absolute;left:162px;top:162px;display:flex;gap:12px}
.logos div{width:116px;height:80px;border:1px solid var(--line);display:flex;align-items:center;justify-content:center;font-weight:700;font-size:15px;color:#222}

/* footer */
.footer{position:absolute;left:0;top:2628px;width:1200px;height:302px;background:#2a2a2a;color:#ddd}
.footer .left{position:absolute;left:0;top:0;width:483px;height:302px;background:#1e1e1e}
.footer h5{position:absolute;font-family:"Tinos",serif;font-weight:400;font-size:17px;color:#fff}
.footer p{font-size:10.5px;line-height:18px}
.fsocial{position:absolute;left:162px;top:2863px;display:flex;gap:6px}
.cities{position:absolute;font-size:10.5px;line-height:22.5px;list-style:none}
.cities li::before{content:"›";margin-right:8px}
.copy{position:absolute;left:0;top:2930px;width:1200px;height:40px;background:#fff;font-size:11px;color:#333}
</style>
</head>
<body>

<header class="hero">
  <div class="hero-map" role="img" aria-label="World map marking property locations with location pins"></div>

  <div class="topbar">
    <div class="social"><span></span><span class="on"></span><span></span><span></span><span></span></div>
    <div class="lang"><i></i>English
      <svg width="8" height="6" viewBox="0 0 8 6"><path d="M1 1l3 3 3-3" stroke="#eee" fill="none"/></svg></div>
    <div class="call">
      <svg width="14" height="14" viewBox="0 0 24 24"><path fill="#eee" d="M6.6 10.8a15 15 0 006.6 6.6l2.2-2.2c.3-.3.7-.4 1-.2 1.1.4 2.3.6 3.6.6.6 0 1 .4 1 1V20c0 .6-.4 1-1 1A17 17 0 013 4c0-.6.4-1 1-1h3.5c.6 0 1 .4 1 1 0 1.3.2 2.5.6 3.6.1.3 0 .7-.2 1z"/></svg>
      Call : 0123 456 789</div>
  </div>

  <nav class="navbar">
    <div class="brand"><b></b><span>Vento Hallmark</span></div>
    <div class="menu">
      <a class="active" style="left:0">Home</a>
      <a style="left:77px">About Us</a>
      <a style="left:174px">Costa del Sol</a>
      <a style="left:292px">Services</a>
      <a style="left:384px">Testimonials</a>
      <a style="left:505px">Contact Us</a>
    </div>
  </nav>

  <svg class="slide-arrow" style="left:62px" width="46" height="80" viewBox="0 0 46 80"><path d="M42 2L4 40l38 38" stroke="#fff" stroke-width="2" fill="none"/></svg>
  <svg class="slide-arrow" style="left:1092px" width="46" height="80" viewBox="0 0 46 80"><path d="M4 2l38 38L4 78" stroke="#fff" stroke-width="2" fill="none"/></svg>
  <div class="dots"><i></i><i class="on"></i><i></i></div>
</header>

<section class="search">
  <div class="search-form"></div>
  <div class="tabs">
    <div class="tab on">
      <svg width="14" height="14" viewBox="0 0 16 16"><circle cx="6.5" cy="6.5" r="5" stroke="#fff" stroke-width="2" fill="none"/><path d="M10 10l5 5" stroke="#fff" stroke-width="2"/></svg>Find Your Home</div>
    <div class="tab off">
      <svg width="14" height="13" viewBox="0 0 16 14"><path d="M8 0L0 7h2v7h4V9h4v5h4V7h2z" fill="#fff"/></svg>House for sell</div>
  </div>
  <div class="dream"><small>DISCOVER YOUR</small><strong>DREAM<br>HOUSE</strong></div>

  <div class="field" style="left:349px;top:85px">Location</div>
  <div class="field" style="left:586px;top:85px">Sub-location</div>
  <div class="field" style="left:824px;top:85px">Status</div>
  <div class="field" style="left:349px;top:143px">No.of Bedrooms</div>
  <div class="field" style="left:586px;top:143px">No.of Bathrooms</div>
  <div class="field" style="left:824px;top:143px">No.of Guest</div>

  <div class="range" style="left:349px;top:192px">No.of Bedrooms
    <div class="track"><div class="fill" style="left:0;width:112px"></div><span class="knob" style="left:-4px"></span><span class="knob" style="left:106px"></span></div></div>
  <div class="range" style="left:586px;top:192px">Area [150 - 720]
    <div class="track"><div class="fill" style="left:51px;width:107px"></div><span class="knob" style="left:45px"></span><span class="knob" style="left:152px"></span></div></div>

  <div class="btn-search">
    <svg width="11" height="11" viewBox="0 0 16 16"><circle cx="6.5" cy="6.5" r="5" stroke="#222" stroke-width="2.4" fill="none"/><path d="M10 10l5 5" stroke="#222" stroke-width="2.4"/></svg>Search Property</div>
</section>

<section class="developments">
  <div class="sec-head abs" style="left:162px;top:46px"><b></b><h2>NEW DEVELOPMENTS</h2></div>
  <div class="abs" style="left:162px;top:90px;width:96px;height:3px;background:var(--navy)"></div>
  <div class="pager" style="left:897px;top:49px">
    <span><svg width="6" height="9" viewBox="0 0 6 9"><path d="M5 1L1 4.5 5 8" stroke="#333" fill="none"/></svg></span>
    <span class="dk"><svg width="6" height="9" viewBox="0 0 6 9"><path d="M1 1l4 3.5L1 8" stroke="#fff" fill="none"/></svg></span>
  </div>
  <div class="view-all">View All</div>

  <div class="cards">
    <article class="card">
      <div class="photo" role="img" aria-label="Modern two-storey villa lit at dusk" style="background:linear-gradient(160deg,#3a3f5a,#7a5a3a 60%,#2e3a22)"></div>
      <h3>EL Rehab Mountain Vills</h3>
      <div class="price">$ 125.000 <em>⌖ Miami, USA</em></div>
      <p>Lorem ipsum dolor sit amet, consec tet uer adipiscing elit, sed diam nonu mmy nibh euismod tincidunt ut laoreet.</p>
      <div class="stats"><span>▣ 320 m2</span><span>▤ 8</span><span>▥ 3</span><span>▦ 2</span></div>
    </article>
    <article class="card">
      <div class="photo" role="img" aria-label="Contemporary house facade at night" style="background:linear-gradient(160deg,#2a2e3a,#5e4a3a 60%,#2a2a2a)"></div>
      <div class="fav"><small>Add To Favourite</small><i style="left:56px"></i><i style="left:83px;background:#fff"></i><i style="left:110px"></i></div>
      <h3>EL Rehab Mountain Vills</h3>
      <div class="price">$ 125.000 <em>⌖ Miami, USA</em></div>
      <p>Lorem ipsum dolor sit amet, consec tet uer adipiscing elit, sed diam nonu mmy nibh euismod tincidunt ut laoreet.</p>
      <div class="stats"><span>▣ 320 m2</span><span>▤ 8</span><span>▥ 3</span><span>▦ 2</span></div>
    </article>
    <article class="card">
      <div class="photo" role="img" aria-label="Single-storey family home with lawn" style="background:linear-gradient(180deg,#8fb3d8,#b9c4cc 55%,#5a7a3a)"></div>
      <span class="sale">Sale</span>
      <h3>EL Rehab Mountain Vills</h3>
      <div class="price">$ 125.000 <em>⌖ Miami, USA</em></div>
      <p>Lorem ipsum dolor sit amet, consec tet uer adipiscing elit, sed diam nonu mmy nibh euismod tincidunt ut laoreet.</p>
      <div class="stats"><span>▣ 320 m2</span><span>▤ 8</span><span>▥ 3</span><span>▦ 2</span></div>
    </article>
    <article class="card">
      <div class="photo" role="img" aria-label="Mediterranean villa with palm trees" style="background:linear-gradient(180deg,#6ea3d6,#c9a27a 55%,#4f7a3a)"></div>
      <span class="sale">Sale</span>
      <h3>EL Rehab Mountain Vills</h3>
      <div class="price">$ 125.000 <em>⌖ Miami, USA</em></div>
      <p>Lorem ipsum dolor sit amet, consec tet uer adipiscing elit, sed diam nonu mmy nibh euismod tincidunt ut laoreet.</p>
      <div class="stats"><span>▣ 320 m2</span><span>▤ 8</span><span>▥ 3</span><span>▦ 2</span></div>
    </article>
  </div>
</section>

<section class="promoted">
  <div class="abs serif" style="left:0;width:1200px;top:43px;text-align:center;font-size:12px">Find Property in YOur City</div>
  <div class="sec-head abs" style="left:428px;top:64px"><b></b><h2>SPECIALLY PROMOTED</h2></div>
  <div class="abs" style="left:562px;top:111px;width:76px;height:2px;background:var(--navy)"></div>

  <div class="tile" style="left:162px;top:133px;width:426px;height:428px" role="img" aria-label="Large suburban house under a pink evening sky">
    <div style="position:absolute;inset:0;background:linear-gradient(180deg,#b58fb0,#d8b6c6 35%,#8a8580 60%,#5a6a3a 80%,#9a9a98)"></div>
    <div class="cap"></div>
    <h4 style="left:12px;bottom:36px;font-size:20px">Laxury Villa</h4>
    <div class="meta" style="left:12px;bottom:18px">33 Properties</div>
    <div class="meta" style="left:268px;bottom:39px">Start From</div>
    <div class="amt" style="right:16px;bottom:35px;font-size:20px">$152.000</div>
    <div class="meta" style="right:16px;bottom:18px">⌖ Miami, USA</div>
  </div>

  <div class="tile" style="left:612px;top:133px;width:426px;height:204px" role="img" aria-label="Villa with illuminated swimming pool at night">
    <div style="position:absolute;inset:0;background:linear-gradient(180deg,#1f2a44,#4a3a2a 55%,#3a5a6a)"></div>
    <div class="cap"></div>
    <h4 style="left:18px;bottom:36px;font-size:19px">Swimming Pool</h4>
    <div class="meta" style="left:18px;bottom:18px">52 Properties</div>
    <div class="meta" style="left:256px;bottom:38px">Start From</div>
    <div class="amt" style="right:34px;bottom:34px;font-size:19px">$143.000</div>
    <div class="meta" style="right:34px;bottom:18px">⌖ Hawai</div>
  </div>

  <div class="tile" style="left:612px;top:361px;width:200px;height:200px" role="img" aria-label="Timber-framed cottage house">
    <div style="position:absolute;inset:0;background:linear-gradient(180deg,#7fa6cc,#8a6a52 50%,#4a5a32)"></div>
    <div class="cap"></div>
    <h4 style="left:12px;bottom:36px;font-size:15px">Cozy houses</h4>
    <div class="meta" style="left:12px;bottom:20px">19 Properties</div>
    <div class="amt" style="right:12px;bottom:36px;font-size:15px">$22.000</div>
    <div class="meta" style="right:12px;bottom:20px">⌖ Maine</div>
  </div>

  <div class="tile" style="left:836px;top:361px;width:202px;height:200px" role="img" aria-label="Grey townhouses with garden">
    <div style="position:absolute;inset:0;background:linear-gradient(180deg,#c9d4dc,#8a8e94 55%,#5a6a4a)"></div>
    <div class="cap"></div>
    <h4 style="left:12px;bottom:36px;font-size:15px">Gardens</h4>
    <div class="meta" style="left:12px;bottom:20px">88 Properties</div>
    <div class="amt" style="right:12px;bottom:36px;font-size:15px">$24.000</div>
    <div class="meta" style="right:12px;bottom:20px">⌖ Miami</div>
  </div>

  <div class="abs" style="left:571px;top:592px;display:flex;gap:6px">
    <i style="width:9px;height:9px;border-radius:50%;background:#bbb"></i>
    <i style="width:9px;height:9px;border-radius:50%;background:#333"></i>
    <i style="width:9px;height:9px;border-radius:50%;background:#bbb"></i>
    <i style="width:9px;height:9px;border-radius:50%;background:#bbb"></i>
  </div>
</section>

<section class="testimonials" role="img" aria-label="Evening view of a lit villa exterior behind client testimonials">
  <div class="sec-head abs" style="left:420px;top:48px"><b style="border-color:#fff"></b><h2 style="color:#fff">CLIENTS TESTIMONIALS</h2></div>
  <div class="abs" style="left:562px;top:94px;width:76px;height:2px;background:#fff"></div>

  <div class="avatar" style="top:147px" role="img" aria-label="Client portrait"></div>
  <div class="avatar" style="top:209px" role="img" aria-label="Client portrait"></div>
  <div class="avatar" style="top:270px" role="img" aria-label="Client portrait"></div>
  <div class="abs" style="left:212px;top:171px;width:47px;height:1px;background:#ddd"></div>
  <div class="abs" style="left:256px;top:168px;width:7px;height:7px;border-radius:50%;background:#fff"></div>

  <svg class="abs" style="left:126px;top:215px" width="14" height="26" viewBox="0 0 14 26"><path d="M12 2L2 13l10 11" stroke="#888" stroke-width="2" fill="none"/></svg>
  <svg class="abs" style="left:1060px;top:215px" width="14" height="26" viewBox="0 0 14 26"><path d="M2 2l10 11L2 24" stroke="#888" stroke-width="2" fill="none"/></svg>

  <div class="quote-box">
    <svg class="abs" style="left:364px;top:-8px" width="50" height="40" viewBox="0 0 50 40"><path d="M2 20Q2 4 20 2v8Q11 12 11 20h9v18H2zM28 20q0-16 18-18v8q-9 2-9 10h9v18H28z" fill="#fff"/></svg>
    <p>Lorem Ipsum is simply dummy text of the printing and typesetting industry. Lorem Ipsum has been the industry's standard dummy text ever since the 1500s, when an unknown printer took a galley of type and scrambled it to make a type specimen book. It has survived not only five centuries, but mmy text ever since the 1500s, when an unknown printer took a galley of type and scrambalso the leap into electronic typesetting, remaining essentiall.</p>
    <cite>- Mr. John Doe, Company Name</cite>
  </div>
</section>

<section class="clients">
  <div class="sec-head abs" style="left:438px;top:46px"><b></b><h2>OUR VALUED CLIENTS</h2></div>
  <p class="abs" style="left:250px;top:112px;width:700px;text-align:center;font-size:11px;line-height:20px;color:#333">Lorem Ipsum is simply dummy text of the printing and typesetting industry. Lorem Ipsum has been the industry's standard dummy text ever since the 1500s, when an unknow.</p>
  <div class="logos">
    <div>Trelvane</div><div>Phasewise</div><div>Hopperly</div><div>Ledgerline</div><div>Arcwell</div><div>Nodara</div><div>Phasewise</div>
  </div>
  <div class="pager" style="left:574px;top:262px">
    <span><svg width="6" height="9" viewBox="0 0 6 9"><path d="M5 1L1 4.5 5 8" stroke="#333" fill="none"/></svg></span>
    <span style="background:var(--navy)"><svg width="6" height="9" viewBox="0 0 6 9"><path d="M1 1l4 3.5L1 8" stroke="#fff" fill="none"/></svg></span>
  </div>
</section>

<footer class="footer">
  <div class="left"></div>
  <div class="abs" style="left:162px;top:44px;width:50px;height:50px;border:4px solid #ddd"></div>
  <p class="abs" style="left:162px;top:124px;width:290px">Lorem Ipsum is simply dummy text of the printing and typesetting industry. Lorem Ipsum has been the industry's standard dummy text ever since the 1500s, when an unknown prik a galley.</p>

  <h5 style="left:529px;top:40px">Get In Touch</h5>
  <svg class="abs" style="left:531px;top:88px" width="10" height="14" viewBox="0 0 10 14"><path d="M5 0a5 5 0 00-5 5c0 4 5 9 5 9s5-5 5-9a5 5 0 00-5-5zm0 7a2 2 0 110-4 2 2 0 010 4z" fill="#ddd"/></svg>
  <div class="abs" style="left:554px;top:88px;font-size:10.5px;font-weight:700;color:#fff">VENTO HALLMARK</div>
  <p class="abs" style="left:554px;top:106px;width:130px;color:#bbb">Lorem Ipsum is simply dummy text of the printing and typesetting</p>
  <svg class="abs" style="left:530px;top:180px" width="12" height="12" viewBox="0 0 24 24"><path fill="#ddd" d="M6.6 10.8a15 15 0 006.6 6.6l2.2-2.2c.3-.3.7-.4 1-.2 1.1.4 2.3.6 3.6.6.6 0 1 .4 1 1V20c0 .6-.4 1-1 1A17 17 0 013 4c0-.6.4-1 1-1h3.5c.6 0 1 .4 1 1 0 1.3.2 2.5.6 3.6.1.3 0 .7-.2 1z"/></svg>
  <div class="abs" style="left:554px;top:178px;font-size:10.5px;color:#bbb">(0123) 456 789</div>
  <svg class="abs" style="left:530px;top:216px" width="13" height="10" viewBox="0 0 13 10"><rect x=".5" y=".5" width="12" height="9" fill="#ddd"/><path d="M1 1l5.5 4.5L12 1" stroke="#1e1e1e" fill="none"/></svg>
  <div class="abs" style="left:554px;top:213px;font-size:10.5px;color:#bbb">info@ventohallmark.example</div>

  <h5 style="left:828px;top:40px">Property Cities</h5>
  <ul class="cities" style="left:840px;top:80px">
    <li>Alaska</li><li>California</li><li>colorado</li><li>Florida</li><li>Kansas</li><li>Louisiana</li><li>Michigan</li>
  </ul>
  <ul class="cities" style="left:962px;top:80px">
    <li>Mississippi</li><li>New Jersey</li><li>New York</li><li>Oklahoma</li><li>Texas</li><li>Washington</li><li>Wisconsin</li>
  </ul>
</footer>

<div class="fsocial">
  <span style="width:22px;height:22px;background:#333;display:block"></span>
  <span style="width:22px;height:22px;background:#333;display:block"></span>
  <span style="width:22px;height:22px;background:#fff;display:block"></span>
  <span style="width:22px;height:22px;background:#333;display:block"></span>
  <span style="width:22px;height:22px;background:#333;display:block"></span>
</div>

<div class="copy">
  <span class="abs" style="left:162px;top:13px">© Copyright 2016, Vento Hallmark. All Right Reserved.</span>
  <span class="abs" style="left:596px;top:13px">Home</span>
  <span class="abs" style="left:650px;top:13px;font-weight:700">About Us</span>
  <span class="abs" style="left:724px;top:13px">Costa del Sol</span>
  <span class="abs" style="left:816px;top:13px">Services</span>
  <span class="abs" style="left:882px;top:13px">Testimonials</span>
  <span class="abs" style="left:976px;top:13px">Contact Us</span>
</div>

</body>
</html>
```